Verodex business card

Business card for sustainable investment company called "Verodex". Verodex is an exchange platform selling carbon credits between buyers and sellers. Carbon Credits are an environmental commodity for reducing global carbon emissions.

the card should obviously have our logo and the theme should be sustainability/environment mixed with a trading platform.

Contact Information for Business Card

Logo, Name, Title, Phone, Email

Colors
0054AA
0677BA
7BADD7
CADEEF
E8F1F8
0094D4
00A9DD
6FCCEA
C7EBF8
E9F6FB
00AB8E
00BBA5
67D7C9
C6EFE9
E9F9F6
59FF00
82FF00
B8FF75
E3FFCB
F4FFEA

```html
<!DOCTYPE html>
<html lang="en">
<head>
<meta charset="UTF-8">
<title>Verodex Business Card</title>
<link rel="stylesheet" href="https://fonts.googleapis.com/css2?family=Poppins:wght@400;500;600&display=swap">
<style>
  :root {
    --bg: #e2e2e2;
    --card-white: #f6f6f7;
    --ink: #2b3a55;
    --text: #333a44;
    --accent: #1f9fe0;
    --blue-deep: #1d6bdc;
    --blue-mid: #2fa3e2;
    --aqua: #3fdbe2;
    --rule: #3a3a3a;
    --white: #ffffff;
  }
  * { box-sizing: border-box; margin: 0; padding: 0; }
  html, body {
    width: 1200px; height: 1200px; overflow: hidden;
    background: var(--bg);
    font-family: "Poppins", sans-serif;
  }
  .canvas { position: relative; width: 1200px; height: 1200px; }

  .card {
    position: absolute;
    left: 262px;
    width: 686px;
    height: 392px;
    border-radius: 20px;
    overflow: hidden;
  }

  /* Front */
  .card-front { top: 165px; background: var(--card-white); }
  .front-brand {
    position: absolute; right: 57px; top: 224px;
    display: flex; align-items: center; gap: 12px;
    top: 0; margin-top: 224px;
  }
  .card-front .front-brand { top: 0; margin-top: 0; top: 226px; }
  .brand {
    position: absolute;
    display: flex; align-items: center;
    font-weight: 600; letter-spacing: 0.5px; line-height: 1;
  }
  .brand-front { right: 58px; top: 58px; gap: 12px; font-size: 38px; color: var(--ink); }
  .brand-front .brand-dot { width: 22px; height: 22px; border-radius: 50%; background: var(--accent); }

  .person { position: absolute; left: 49px; top: 230px; }
  .person-name { font-size: 24px; font-weight: 600; color: var(--accent); line-height: 1.1; letter-spacing: 0.2px; }
  .person-title { font-size: 15.5px; color: var(--text); margin-top: 2px; }

  .rule { position: absolute; left: 49px; right: 53px; top: 283px; height: 1px; background: var(--rule); }

  .contacts { position: absolute; left: 49px; top: 292px; list-style: none; }
  .contacts li {
    display: flex; align-items: center; gap: 9px;
    font-size: 16.5px; color: var(--text); height: 21px;
  }
  .contacts svg { width: 14px; height: 14px; flex: none; }

  .address {
    position: absolute; right: 53px; top: 292px;
    text-align: right; font-size: 16.5px; color: var(--text); line-height: 21px;
  }

  .front-band {
    position: absolute; left: 0; right: 0; bottom: 0; height: 16px;
    background: linear-gradient(90deg, var(--blue-mid), var(--aqua));
  }

  /* Back */
  .card-back {
    top: 653px;
    background: linear-gradient(45deg, var(--blue-deep) 0%, var(--blue-mid) 45%, var(--aqua) 100%);
  }
  .brand-back {
    left: 50%; top: 50%; transform: translate(-50%, -50%);
    gap: 20px; font-size: 58px; color: var(--white);
  }
  .brand-back .brand-dot { width: 36px; height: 36px; border-radius: 50%; background: var(--white); }
</style>
</head>
<body>
<main class="canvas">
  <section class="card card-front" aria-label="Card front">
    <div class="brand brand-front">
      <span class="brand-dot"></span>
      <span class="brand-name">VERODEX</span>
    </div>

    <div class="person">
      <p class="person-name">DANIEL HART</p>
      <p class="person-title">Managing Director</p>
    </div>

    <div class="rule"></div>

    <ul class="contacts">
      <li>
        <svg viewBox="0 0 16 16" aria-hidden="true"><path fill="#1f9fe0" d="M3.6 1.2l2.3 2.6-1.3 2a8.5 8.5 0 0 0 5.6 5.6l2-1.3 2.6 2.3-1.3 2.2C7.6 16 0 8.4.6 2.5z"/></svg>
        <span>541-302-7186</span>
      </li>
      <li>
        <svg viewBox="0 0 16 16" aria-hidden="true"><rect x="3.5" y="0.8" width="9" height="14.4" rx="1.6" fill="none" stroke="#1f9fe0" stroke-width="1.6"/><circle cx="8" cy="12.6" r="0.9" fill="#1f9fe0"/></svg>
        <span>541-775-2049</span>
      </li>
      <li>
        <svg viewBox="0 0 16 16" aria-hidden="true"><rect x="0.5" y="3" width="15" height="10" rx="1" fill="#3cc9e4"/><path d="M1 3.8l7 5 7-5" fill="none" stroke="#ffffff" stroke-width="1.2"/></svg>
        <span>info@verodex.com</span>
      </li>
    </ul>

    <div class="address">
      <p>4120 Willow Bend Road</p>
      <p>Juneau, Alaska 99801</p>
      <p>www.verodex.com</p>
    </div>

    <div class="front-band"></div>
  </section>

  <section class="card card-back" aria-label="Card back">
    <div class="brand brand-back">
      <span class="brand-dot"></span>
      <span class="brand-name">VERODEX</span>
    </div>
  </section>
</main>
</body>
</html>
```